Stylish Business Cards Wanted

- DOUBLE SIDED Design Required -

High end, edgy cards for a corporate and personal stylist. Must include logo,
Name: Belinda Harwick
Title: Director and Stylist
telephone : +61 8 7142 5809
email: belinda@theloombriefing.example
website: theloombriefing.example
Tag: Corporate Workwear & Uniform Specialist | Personal Stylist
Would like nice icons for telephone, email, website

Target Market(s)

Businesses wanting stylish uniforms, people wanting stylish wardrobes

Industry/Entity Type

Corporate Workwear Stylist

Contact Information for Business Card

I would like black, white and gold foiling incorporated in the design - possibly a touch of the other colours on my branding guide attached Name: Belinda Harwick Title: Director and Stylist telephone : +61 8 7142 5809 email: belinda@theloombriefing.example website: theloombriefing.example Tag: Corporate Workwear & Uniform Specialist | Personal Stylist Would like nice icons for telephone, email, website

Font styles to use
Other font styles liked:
• Raleway

Colors

Designer to choose colors to be used in the design.

Requirements
Must have
• Gold foil accents

```html
<!DOCTYPE html>
<html lang="en">
<head>
<meta charset="utf-8">
<title>The Loom Briefing – Business Cards</title>
<link rel="stylesheet" href="https://fonts.googleapis.com/css2?family=Raleway:wght@400;500;600&display=swap">
<style>
  :root {
    --backdrop: #2b2b2d;
    --card-black: #1f1f20;
    --white: #f2f2f2;
    --gold: #d8b447;
    --gold-light: #f3dc7a;
    --gold-deep: #b38a24;
    --magenta: #9c1560;
  }
  * { box-sizing: border-box; margin: 0; padding: 0; }
  html, body {
    width: 1200px; height: 868px; overflow: hidden;
    background: var(--backdrop);
    font-family: "Raleway", sans-serif;
  }
  .sheet {
    width: 1200px; height: 868px;
    display: flex; align-items: center; justify-content: center; gap: 56px;
  }
  .card {
    position: relative;
    width: 520px; height: 298px;
    background: var(--card-black);
    overflow: hidden;
    border-bottom: 5px solid var(--magenta);
    box-shadow: 0 18px 40px rgba(0,0,0,.45);
  }

  /* Front */
  .lettering-area {
    position: absolute; left: -10px; top: -10px;
    width: 270px; height: 330px;
    background: linear-gradient(135deg, var(--gold-light) 0%, var(--gold) 45%, var(--gold-deep) 100%);
    border-radius: 0 60% 40% 0 / 0 50% 50% 0;
  }
  .contact-block {
    position: absolute; left: 290px; top: 78px; right: 24px;
    text-align: center;
  }
  .contact-name {
    color: var(--white); font-weight: 600; font-size: 19px; letter-spacing: .04em;
    text-transform: uppercase;
  }
  .contact-title { color: var(--gold); font-size: 13px; margin-top: 3px; }
  .divider { width: 34px; height: 1px; background: var(--white); opacity: .7; margin: 16px auto; }
  .contact-list { list-style: none; text-align: left; display: inline-block; }
  .contact-list li {
    display: flex; align-items: center; gap: 8px;
    color: var(--white); font-size: 11.5px; line-height: 21px;
  }
  .icon { width: 12px; height: 12px; flex: none; stroke: var(--gold); fill: none; stroke-width: 1.4; }

  /* Back */
  .brand {
    position: absolute; left: 0; right: 0; top: 96px;
    display: flex; align-items: center; justify-content: center; gap: 10px;
  }
  .brand-mark { width: 12px; height: 12px; background: var(--gold); }
  .brand-name {
    color: var(--white); font-weight: 500; font-size: 30px; letter-spacing: .02em;
  }
  .tagline {
    position: absolute; right: 46px; bottom: 44px;
    color: var(--white); font-size: 10.5px; letter-spacing: .08em;
    text-transform: uppercase; text-align: center; line-height: 15px;
  }
</style>
</head>
<body>
<main class="sheet">
  <section class="card card-front">
    <div class="lettering-area" role="img" aria-label="Large gold foil hand-lettered script word"></div>
    <div class="contact-block">
      <h1 class="contact-name">Belinda Harwick</h1>
      <p class="contact-title">Director &amp; Stylist</p>
      <div class="divider"></div>
      <ul class="contact-list">
        <li>
          <svg class="icon" viewBox="0 0 12 12"><path d="M2.5 1.2l2 2.3-1 1.2a6 6 0 0 0 3.8 3.8l1.2-1 2.3 2-1.3 1.3C5.5 10.6 1.4 6.5 1.2 2.5z"/></svg>
          +61 8 7142 5809
        </li>
        <li>
          <svg class="icon" viewBox="0 0 12 12"><rect x="1" y="2.5" width="10" height="7"/><path d="M1 2.5l5 4 5-4"/></svg>
          belinda@theloombriefing.example
        </li>
        <li>
          <svg class="icon" viewBox="0 0 12 12"><circle cx="6" cy="6" r="5"/><ellipse cx="6" cy="6" rx="2.2" ry="5"/><path d="M1 6h10"/></svg>
          theloombriefing.example
        </li>
      </ul>
    </div>
  </section>

  <section class="card card-back">
    <div class="brand">
      <span class="brand-mark"></span>
      <span class="brand-name">The Loom Briefing</span>
    </div>
    <p class="tagline">Corporate Workwear<br>Uniform Specialist<br>Personal Stylist</p>
  </section>
</main>
</body>
</html>
```